Brovan - Web Design Rebrand for Manufacturing Automation Company

I need a new brand for a customer based in Ireland.
The website currently: https://corvethsystems.example/
Corveth Systems provides a wide range of automation and IT solutions used in manufacturing operations.
Their solutions span a broad spectrum of technology from physical machines and robots to cloud based management solutions for these systems.
They are an Authorised Distributor for Pelmont Controls.
Their partnership with Pelmont Controls will now include working closely to keep track of supply trends and preparing customers for future Data Centre projects.

Essentially their USP:
They have a large team of specialist technical people spanning the breadth of skills to be able to deploy and support automation and IT solutions in manufacturing in the Life Sciences Industry.

Along with Pelmont Controls, they have specialist teams for accelerating Data Center applications.

Competitor websites:
https://www.duravex.example/global/en.html - I really like the layout of their partnerships/collaborations section.
https://global.qtl.example/group/en - Their first moving imagery/tagline and 'discover more' when you enter the site is really eye-catching.
https://www.kv.example/uk/en/ - They layout and structure of the 'The core of what we do section' is really nice.

These are a big companies so anything we could steal would be good 😊

They want:
• Fresh, sharp imagery
• Movement on the main page and perhaps video on some sections? - similar to QTL
• A page to showcase Automation Solutions
• A page to showcase Data Centers
• About us
• Sectors they operate in (includes Life Sciences, Food & Bev, Data Centres)

Industry/Entity Type

Life Science Manufacturing

Number of Pages Required

1 page

Font styles to use
Sans Serif

Colors
0054AA
0677BA
7BADD7
CADEEF
E8F1F8

Requirements
Must have
• Moving Imagery

```html
<!DOCTYPE html>
<html lang="en">
<head>
<meta charset="utf-8">
<title>Corveth Systems – Automation, IT and Data Centre Solutions</title>
<link href="https://fonts.googleapis.com/css2?family=Poppins:wght@300;400;500;600;700&display=swap" rel="stylesheet">
<style>
:root{
  --navy:#0b1a33;
  --navy-deep:#071226;
  --blue:#0054aa;
  --blue-mid:#0677ba;
  --sky:#1aa3e0;
  --blue-soft:#7badd7;
  --blue-pale:#cadeef;
  --blue-mist:#e8f1f8;
  --ink:#1b2433;
  --muted:#6b7482;
  --line:#e3e8ee;
  --white:#ffffff;
  --grey-bg:#f1f3f6;
}
*{box-sizing:border-box;margin:0;padding:0}
html,body{width:1200px;height:3856px;overflow:hidden}
body{font-family:"Poppins",sans-serif;color:var(--ink);background:var(--white);position:relative}
.abs{position:absolute}
.eyebrow{font-size:12px;font-weight:600;letter-spacing:1.5px;color:var(--blue-mid);text-transform:uppercase}
.section-title{font-size:30px;font-weight:600;color:var(--ink);line-height:1.25}
.center{text-align:center;left:0;width:1200px}
.btn{display:inline-block;background:var(--sky);color:var(--white);font-size:12px;font-weight:500;padding:10px 22px;border-radius:3px}

/* header */
.site-header{top:0;left:0;width:1200px;height:100px;background:var(--white);border-bottom:1px solid var(--line)}
.contact-row{top:10px;left:150px;font-size:11px;color:var(--muted);display:flex;gap:28px}
.contact-row span{display:flex;align-items:center;gap:6px}
.brand{top:40px;left:150px;display:flex;align-items:center;gap:10px;font-size:17px;font-weight:600;color:var(--blue);letter-spacing:.5px}
.brand i{width:22px;height:22px;background:var(--blue);display:block}
.main-nav{top:60px;left:440px;display:flex;gap:30px;font-size:13px;color:var(--ink)}
.header-cta{top:50px;left:920px}

/* hero */
.hero{top:100px;left:0;width:1200px;height:540px;background:radial-gradient(ellipse at 30% 70%,#0f5aa8 0%,#0a2f66 35%,var(--navy-deep) 75%)}
.hero h1{top:230px;font-size:38px;font-weight:600;color:var(--white)}
.hero p{top:292px;font-size:16px;color:var(--blue-pale)}
.play{top:445px;left:570px;width:60px;height:60px}
.discover{top:528px;font-size:11px;letter-spacing:2px;color:var(--white);font-weight:500}

/* partners */
.partners-eyebrow{top:700px}
.partners-title{top:728px}
.partner{top:830px;height:110px;width:230px;display:flex;align-items:center;justify-content:center;gap:10px;font-size:22px;font-weight:600;color:var(--ink)}
.partner.active{background:var(--white);box-shadow:0 6px 22px rgba(0,40,90,.14);border-bottom:3px solid var(--sky)}
.partner i{width:18px;height:18px;display:block;border-radius:50%}

/* about */
.about-eyebrow{top:1068px}
.about-title{top:1095px}
.about-photo{top:1280px;left:140px;width:470px;height:300px;background:linear-gradient(135deg,#3a4a66,#8a6a52 55%,#c8b49a);border-radius:4px}
.about-badge{top:1360px;left:365px;width:300px;height:225px;background:var(--white);box-shadow:0 10px 30px rgba(0,0,0,.18);border-radius:4px;display:flex;flex-direction:column;align-items:center;justify-content:center;gap:16px}
.about-badge i{width:70px;height:70px;background:var(--blue);display:block}
.about-badge span{font-size:18px;font-weight:600;color:var(--navy);letter-spacing:1px}
.story{top:1290px;left:665px;width:400px}
.story h3{font-size:15px;font-weight:600;margin-bottom:10px}
.story ul{list-style:none}
.story li{font-size:11.5px;color:var(--muted);line-height:1.6;margin-bottom:8px;padding-left:14px;position:relative}
.story li:before{content:"";position:absolute;left:0;top:7px;width:5px;height:5px;background:var(--sky);border-radius:50%}
.story .btn{margin-top:14px}

/* solutions */
.solutions{top:1640px;left:0;width:1200px;height:800px;background:var(--grey-bg)}
.sol-eyebrow{top:1770px;left:140px}
.sol-title{top:1792px;left:140px;width:420px;font-size:30px}
.sol-intro{top:1795px;left:610px;width:450px;font-size:12px;color:var(--muted);line-height:1.7}
.cards{top:1940px;left:140px;display:flex;width:920px}
.card{width:230px;height:340px;background:var(--white);padding:34px 22px;border-right:1px solid var(--line)}
.card svg{display:block;margin-bottom:18px}
.card h4{font-size:14px;font-weight:600;line-height:1.35;margin-bottom:14px}
.card p{font-size:11px;color:var(--muted);line-height:1.65;margin-bottom:20px}
.card .more{font-size:11px;font-weight:500;display:flex;align-items:center;gap:8px}
.card .more b{width:18px;height:18px;border-radius:50%;background:var(--blue);display:inline-block}
.card.active{background:var(--sky);color:var(--white)}
.card.active p{color:var(--blue-mist)}
.card.active .more b{background:var(--white)}
.arrow{top:2090px;width:32px;height:32px;background:var(--white);border-radius:50%;box-shadow:0 2px 8px rgba(0,0,0,.12)}
.dots{top:2320px;left:565px;display:flex;gap:6px}
.dots i{width:14px;height:3px;background:var(--blue-soft);display:block}
.dots i.on{width:24px;background:var(--blue)}

/* sectors */
.sec-eyebrow{top:2512px}
.sec-title{top:2540px}
.sector{top:2640px;width:398px;height:420px;display:flex;align-items:flex-end;justify-content:center;padding-bottom:26px;color:var(--white);font-size:18px;font-weight:500}
.sector.life{left:0;background:linear-gradient(160deg,#5f6e82,#2a3546 70%)}
.sector.food{left:401px;background:linear-gradient(160deg,#6b4a32,#2c2018)}
.sector.data{left:802px;background:linear-gradient(160deg,#1d4f8a,#0a1f3f 70%)}
.food-overlay{top:2660px;left:440px;width:320px;text-align:center;color:var(--white)}
.food-overlay h4{font-size:18px;font-weight:600;margin-bottom:10px}
.food-overlay p{font-size:11px;line-height:1.7;color:#e8e1da}

/* customers */
.customers{top:3080px;left:0;width:1200px;height:390px;background:var(--sky)}
.cus-eyebrow{top:3120px;color:var(--white)}
.cus-title{top:3145px;color:var(--white)}
.clients{top:3240px;left:60px;display:flex;gap:18px}
.client{width:200px;height:86px;background:var(--white);display:flex;align-items:center;justify-content:center;gap:8px;font-size:20px;font-weight:600;color:var(--navy)}
.client i{width:14px;height:14px;background:var(--blue);display:block}
.cus-line{top:3385px;left:140px;width:920px;height:2px;background:rgba(255,255,255,.45)}
.cus-line i{display:block;width:300px;height:2px;background:var(--white)}

/* footer */
.site-footer{top:3470px;left:0;width:1200px;height:386px;background:var(--navy-deep);color:var(--white)}
.foot-brand{top:3520px;left:140px;width:250px}
.foot-brand .name{display:flex;align-items:center;gap:10px;font-size:20px;font-weight:600;letter-spacing:1px;margin-bottom:16px}
.foot-brand .name i{width:30px;height:30px;background:var(--sky);display:block}
.foot-brand p{font-size:12px;color:#b8c3d3;line-height:1.7}
.foot-col{top:3530px}
.foot-col h5{font-size:14px;font-weight:600;letter-spacing:1.5px;margin-bottom:20px}
.foot-col li{list-style:none;font-size:12px;color:#b8c3d3;margin-bottom:14px;display:flex;align-items:center;gap:10px}
.foot-col li b{width:22px;height:22px;border-radius:50%;background:var(--blue-mid);display:inline-block}
.copyright{top:3790px;left:0;width:1200px;border-top:1px solid rgba(255,255,255,.12);padding-top:22px;text-align:center;font-size:11px;color:#93a0b4}
</style>
</head>
<body>

<header class="site-header abs">
  <div class="contact-row abs">
    <span><svg width="12" height="12" viewBox="0 0 24 24"><path d="M6 2l4 4-2 3c1 3 4 6 7 7l3-2 4 4-3 4C10 22 2 14 2 5z" fill="#0677ba"/></svg>Call: +353 1 555 0142</span>
    <span><svg width="13" height="11" viewBox="0 0 26 20"><rect x="1" y="1" width="24" height="18" fill="none" stroke="#0677ba" stroke-width="2"/><path d="M1 1l12 10L25 1" fill="none" stroke="#0677ba" stroke-width="2"/></svg>Email: info@corvethsystems.example</span>
  </div>
  <div class="brand abs"><i></i>CORVETH SYSTEMS</div>
  <nav class="main-nav abs"><span>About Us</span><span>Automation Solutions</span><span>Data Centers</span><span>Contact</span></nav>
  <span class="btn header-cta abs">TALK TO EXPERT</span>
</header>

<section class="hero abs" role="img" aria-label="Moving imagery of a glowing blue digital network over a data centre">
  <h1 class="abs center" style="text-align:center">Your Automation, IT and Data Centre Solutions Provider</h1>
  <p class="abs center" style="text-align:center">A Pelmont Controls Distributor Specialising in Life Sciences and Data Centres</p>
  <svg class="play abs" viewBox="0 0 60 60"><circle cx="30" cy="30" r="28" fill="none" stroke="#fff" stroke-width="2"/><path d="M24 19l17 11-17 11z" fill="#fff"/></svg>
  <div class="discover abs center" style="text-align:center;top:428px">DISCOVER MORE</div>
</section>

<div class="eyebrow abs center partners-eyebrow" style="text-align:center">Our Partners</div>
<h2 class="section-title abs center partners-title" style="text-align:center">Corveth Technology Partners</h2>
<div class="partner abs" style="left:100px"><i style="background:#c9302c"></i>Ferrolink</div>
<div class="partner active abs" style="left:345px"><i style="background:#0677ba"></i>Netvana</div>
<div class="partner abs" style="left:590px"><i style="background:#0054aa"></i>Orvax</div>
<div class="partner abs" style="left:835px"><i style="background:#c9302c"></i>Calmeric</div>

<div class="eyebrow abs center about-eyebrow" style="text-align:center">About Us</div>
<h2 class="section-title abs center about-title" style="text-align:center">Revolutionizing Manufacturing through Automation</h2>
<div class="about-photo abs" role="img" aria-label="Photo of two engineers inspecting electronic equipment in a lab"></div>
<div class="about-badge abs"><i></i><span>CORVETH SYSTEMS</span></div>
<div class="story abs">
  <h3>Our Story</h3>
  <ul>
    <li>Corveth Systems provides a wide range of automation and IT solutions used in manufacturing operations.</li>
    <li>Our solutions span a broad spectrum of technology from physical machines and robots to cloud based management solutions for these systems.</li>
    <li>Along with Pelmont Controls, we work closely to keep track of supply trends and ready customers for future Data Centre projects.</li>
    <li>We have a large team of specialist technical people spanning the breadth of skills to deploy and support these technologies.</li>
    <li>Orvax Robotics Solutions' official distributor.</li>
  </ul>
  <span class="btn">Learn More</span>
</div>

<section class="solutions abs"></section>
<div class="eyebrow abs sol-eyebrow">Automation Solutions</div>
<h2 class="section-title abs sol-title">Innovating Industries with Robotics &amp; Automation Solutions</h2>
<p class="abs sol-intro">Welcome to Robotics and Automation Solutions, where we pioneer cutting-edge technologies to optimize productivity and streamline operations. Our mission is to provide innovative solutions that streamline processes and enhance efficiency.</p>
<div class="cards abs">
  <div class="card"><svg width="30" height="30" viewBox="0 0 30 30"><ellipse cx="15" cy="7" rx="11" ry="4" fill="none" stroke="#0054aa" stroke-width="2"/><path d="M4 7v16c0 2 5 4 11 4s11-2 11-4V7M4 15c0 2 5 4 11 4s11-2 11-4" fill="none" stroke="#0054aa" stroke-width="2"/></svg><h4>Data<br>Architecture</h4><p>Robust data models that connect plant floor systems with business tools for clear, reliable insight.</p><span class="more"><b></b>Read More</span></div>
  <div class="card"><svg width="30" height="30" viewBox="0 0 30 30"><rect x="3" y="4" width="24" height="18" fill="none" stroke="#0054aa" stroke-width="2"/><path d="M10 27h10M15 22v5" stroke="#0054aa" stroke-width="2"/></svg><h4>Manufacturing<br>Database</h4><p>Secure production databases that capture batch records and keep every line running to plan.</p><span class="more"><b></b>Read More</span></div>
  <div class="card active"><svg width="30" height="30" viewBox="0 0 30 30"><circle cx="15" cy="15" r="5" fill="none" stroke="#fff" stroke-width="2"/><path d="M15 2v6M15 22v6M2 15h6M22 15h6" stroke="#fff" stroke-width="2"/></svg><h4>Robotics<br>&amp; Mechatronics</h4><p>Robot cells and motion systems designed, built and supported by our own specialist engineers.</p><span class="more"><b></b>Read More</span></div>
  <div class="card"><svg width="30" height="30" viewBox="0 0 30 30"><rect x="4" y="3" width="22" height="8" fill="none" stroke="#0054aa" stroke-width="2"/><rect x="4" y="14" width="22" height="8" fill="none" stroke="#0054aa" stroke-width="2"/><path d="M15 22v5" stroke="#0054aa" stroke-width="2"/></svg><h4>IT<br>Infrastructure</h4><p>Networks, servers and cloud platforms sized for regulated sites and growing data centre needs.</p><span class="more"><b></b>Read More</span></div>
</div>
<svg class="arrow abs" style="left:60px" viewBox="0 0 32 32"><path d="M19 10l-6 6 6 6" fill="none" stroke="#1b2433" stroke-width="2"/></svg>
<svg class="arrow abs" style="left:1108px" viewBox="0 0 32 32"><path d="M13 10l6 6-6 6" fill="none" stroke="#1b2433" stroke-width="2"/></svg>
<div class="dots abs"><i class="on"></i><i></i><i></i></div>

<div class="eyebrow abs center sec-eyebrow" style="text-align:center">We Operate In</div>
<h2 class="section-title abs center sec-title" style="text-align:center">Seamless Operations: Transforming Manufacturing<br>with Automation</h2>
<div class="sector life abs" role="img" aria-label="Photo of a life sciences professional using a digital interface">Life Sciences</div>
<div class="sector food abs" role="img" aria-label="Photo of a food and beverage production line"></div>
<div class="food-overlay abs">
  <h4>Food &amp; Bev</h4>
  <p>We help food and beverage producers raise output and keep quality consistent. From packing lines and robot palletising to recipe control and traceability, our teams design, install and support systems that keep plants safe, hygienic and efficient while meeting strict industry rules. Every project is backed by local service and long term support.</p>
</div>
<div class="sector data abs" role="img" aria-label="Photo of glowing network connections in a data centre">Data Centres</div>

<section class="customers abs"></section>
<div class="eyebrow abs center cus-eyebrow" style="text-align:center">Our Customers</div>
<h2 class="section-title abs center cus-title" style="text-align:center">Corveth Technology Customers</h2>
<div class="clients abs">
  <div class="client"><i></i>Keldra</div>
  <div class="client"><i></i>Ornavo</div>
  <div class="client"><i></i>Bellwyn</div>
  <div class="client"><i></i>Tessaro</div>
  <div class="client"><i></i>Virelle</div>
</div>
<div class="cus-line abs"><i></i></div>

<footer class="site-footer abs"></footer>
<div class="foot-brand abs">
  <div class="name"><i></i>CORVETH<br>SYSTEMS</div>
  <p>We provide a wide range of automation and IT solutions used in manufacturing operations.</p>
</div>
<div class="foot-col abs" style="left:560px"><h5>QUICK LINKS</h5><ul><li>About Us</li><li>Automation Solutions</li><li>Data Centers</li><li>Contact</li></ul></div>
<div class="foot-col abs" style="left:740px"><h5>USEFULL LINKS</h5><ul><li>Contact</li><li>Privacy Policy</li><li>Terms &amp; Conditions</li></ul></div>
<div class="foot-col abs" style="left:920px"><h5>FOLLOW US</h5><ul><li><b></b>Flitter</li><li><b></b>Worknet</li><li><b></b>Viewtube</li></ul></div>
<div class="copyright abs">Copyright © 2024 Corveth Systems Manufacturing Automation | All Right Reserved.</div>

</body>
</html>
```